Brightfield Ventures Inc. Letterhead

Creation of attractive and eye catching letterhead for a business start-up for the construction industry. Letterhead must relate to construction, but avoid standard hammer and tools in the design.

I forgot to add some details, sorry about that. Some pertinent info: Ph: 916-555-0187 brightfieldventures.example 448 Willowmere Ave, Ste 210 Folsom, CA 95999 info@brightfieldventures.example not sure if slogan should be in there" “Connecting construction professionals to create a purpose driven industry.” must be able to be used in word. Thanks!

```html
<!DOCTYPE html>
<html lang="en">
<head>
<meta charset="utf-8">
<title>Brightfield Ventures Inc. Letterhead</title>
<link href="https://fonts.googleapis.com/css2?family=Open+Sans:wght@400;600;700&display=swap" rel="stylesheet">
<style>
  :root {
    --backdrop: #e4e4e4;
    --paper: #fbfbfb;
    --brand-red: #c0141b;
    --brand-navy: #121e5a;
    --ink: #3a3a3a;
    --ink-soft: #555555;
  }
  * { box-sizing: border-box; margin: 0; padding: 0; }
  html, body { width: 1200px; height: 945px; overflow: hidden; }
  body {
    background: var(--backdrop);
    font-family: "Open Sans", Arial, sans-serif;
    color: var(--ink);
  }
  .letterhead {
    position: absolute;
    left: 250px; top: 20px;
    width: 700px; height: 905px;
    background: var(--paper);
    box-shadow: 0 4px 16px rgba(0,0,0,0.12);
    overflow: hidden;
  }
  .top-rule { position: absolute; top: 0; height: 5px; }
  .top-rule--red { left: 0; width: 62%; background: var(--brand-red); }
  .top-rule--navy { left: 63%; right: 0; background: var(--brand-navy); }

  .brand {
    position: absolute; left: 70px; top: 62px;
    display: flex; align-items: center; gap: 8px;
  }
  .brand__mark { width: 12px; height: 12px; background: var(--brand-red); }
  .brand__name {
    font-size: 17px; font-weight: 700; color: var(--brand-navy);
    letter-spacing: 0.5px;
  }

  .contact {
    position: absolute; right: 60px; top: 30px;
    list-style: none; font-size: 8.5px; line-height: 12px; color: var(--ink);
  }
  .contact li { display: flex; align-items: flex-start; gap: 5px; }
  .contact svg { width: 8px; height: 8px; margin-top: 2px; flex: none; }

  .letter-body {
    position: absolute; left: 80px; top: 215px; width: 540px;
    font-size: 12.5px; line-height: 17px; color: var(--ink-soft);
  }
  .salutation { font-weight: 700; font-size: 15px; color: var(--ink); margin-bottom: 10px; }
  .letter-body p { margin-bottom: 17px; }
  .letter-body p.indented { padding-left: 40px; }

  .signature {
    position: absolute; left: 120px; top: 565px;
    width: 150px; height: 45px;
    background: linear-gradient(90deg, #e6e6e6, #d6d6d6);
  }

  .footer-swoosh { position: absolute; left: 0; bottom: 0; width: 700px; height: 130px; }
</style>
</head>
<body>
  <main class="letterhead">
    <div class="top-rule top-rule--red"></div>
    <div class="top-rule top-rule--navy"></div>

    <div class="brand">
      <span class="brand__mark"></span>
      <span class="brand__name">BRIGHTFIELD VENTURES</span>
    </div>

    <ul class="contact">
      <li>
        <svg viewBox="0 0 10 10"><path d="M2 1l2 2-1 1.2c.6 1.2 1.6 2.2 2.8 2.8L7 6l2 2-1.3 1.3C4.5 9 1 5.5.7 2.3z" fill="var(--brand-red)"/></svg>
        <span>916-555-0187</span>
      </li>
      <li>
        <svg viewBox="0 0 10 10"><rect x="0.5" y="2" width="9" height="6" fill="var(--brand-red)"/><path d="M0.5 2l4.5 3.5L9.5 2" stroke="#fff" fill="none" stroke-width="0.8"/></svg>
        <span>info@brightfieldventures.example</span>
      </li>
      <li>
        <svg viewBox="0 0 10 10"><circle cx="5" cy="5" r="4.3" fill="none" stroke="var(--brand-red)" stroke-width="1.2"/><circle cx="5" cy="5" r="1.6" fill="var(--brand-red)"/></svg>
        <span>brightfieldventures.example</span>
      </li>
      <li>
        <svg viewBox="0 0 10 10"></svg>
        <span>448 Willowmere Ave, Ste 210,<br>Folsom, CA 95999</span>
      </li>
    </ul>

    <section class="letter-body">
      <h1 class="salutation">Dear Mr. Carver,</h1>
      <p>Lorem Ipsum is simply dummy text of the printing and typesetting industry. Lorem Ipsum has been the industry's standard dummy text ever since the 1500s, when an unknown printer took a galley of type and scrambled it to make a type specimen book. It has survived not only five centuries, but also the leap into electronic typesetting, remaining essentially unchanged.</p>
      <p class="indented">The standard chunk of Lorem Ipsum used since the 1500s is reproduced below for those interested. Sections 1.10.32 and 1.10.33 from "de Structuris Domorum" by Aurelio Pennant are also reproduced in their exact original form, accompanied by English versions from the 1914 translation by H. Marlow.</p>
      <p class="indented">Lorem Ipsum is simply dummy text of the printing and typesetting industry. Lorem Ipsum has been the industry's standard dummy text ever since the 1500s, when an unknown printer took a galley of type and scrambled it to make a type specimen book. It has survived not only five centuries, but also the leap into electronic typesetting, remaining essentially unchanged. It was popularised in the</p>
    </section>

    <div class="signature" role="img" aria-label="Handwritten signature of the sender"></div>

    <svg class="footer-swoosh" viewBox="0 0 700 130" preserveAspectRatio="none" aria-hidden="true">
      <path d="M0 78 Q440 66 700 0 L700 7 Q450 80 0 92 Z" fill="var(--brand-navy)"/>
      <path d="M0 99 Q460 88 700 16 L700 130 L0 130 Z" fill="var(--brand-red)"/>
    </svg>
  </main>
</body>
</html>
```